Bright Towns Forum PowerPoint Design Template and Sample Deck

The Bright Towns Forum is an international organization that seeks to improve the livability, workability and sustainability of the world’s cities.
We seek a versatile PowerPoint design template with 10 slide types plus a “self-documenting” sample deck. Your design will be used in keynote speeches and workshops around the world.
After the contest is completed, we will ask the winning designer to add 10-20 additional slide types for $75 per slide. We also seek a long-term relationship whereby we can request “custom” slides and/or ask the designer to touch up the slides we build to make them better.
FILES. We have uploaded several files:
2. PALETTE. Shows our official colors.
3 LOGOS. Several individual files with different variations of our logo. Some with our motto, some without.
2. SAMPLE SLIDES. Because we were unable to successfully upload our sample deck, we are making it available via this FileNook link:
https://www.filenook-example.com/s/k7qrtmzp2wd9hxa/The%20Bright%20Towns%20Forum%20Design%20Contest%20Notes.docx?dl=0
Target Market(s)
Mayors, department heads, CIOs, senior executives from technology companies
Industry/Entity Type
Information Technology
Colors
Designer to choose colors to be used in the design.
Requirements
Must have
- Please see uploaded Word document for requirements, nice to haves and should not haves and uploaded palette for color preferences.
Nice to have
- see above
Should not have
- see above

```html
<!DOCTYPE html>
<html lang="en">
<head>
<meta charset="utf-8">
<title>Timeline Slide</title>
<link rel="stylesheet" href="https://fonts.googleapis.com/css2?family=Arimo:wght@400&family=Open+Sans:wght@700&display=swap">
<style>
  :root {
    --navy: #002b5c;
    --white: #ffffff;
    --photo-dark: #3b4048;
    --photo-mid: #6b6f76;
    --photo-warm: #8a7f78;
    --overlay: rgba(40, 46, 58, 0.55);
  }
  html, body {
    margin: 0;
    padding: 0;
    width: 1200px;
    height: 675px;
    overflow: hidden;
    background: var(--photo-dark);
  }
  .slide {
    position: relative;
    width: 1200px;
    height: 675px;
    overflow: hidden;
    font-family: "Open Sans", Arial, sans-serif;
    color: var(--white);
  }
  .slide__photo {
    position: absolute;
    inset: 0;
    background:
      linear-gradient(var(--overlay), var(--overlay)),
      radial-gradient(ellipse at 45% 30%, var(--photo-warm) 0%, transparent 45%),
      radial-gradient(ellipse at 78% 35%, #9a8a80 0%, transparent 40%),
      linear-gradient(100deg, #4a5a70 0%, var(--photo-mid) 40%, #5c6068 70%, #4c5a6c 100%);
  }
  .slide__title {
    position: absolute;
    left: 61px;
    top: 52px;
    margin: 0;
    font-family: "Arimo", Arial, sans-serif;
    font-weight: 400;
    font-size: 49px;
    line-height: 1;
    letter-spacing: 0.2px;
  }
  .timeline {
    position: absolute;
    inset: 0;
  }
  .milestone-note {
    position: absolute;
    width: 240px;
    margin: 0;
    font-size: 16px;
    font-weight: 700;
    line-height: 24px;
    text-align: center;
  }
  .milestone-note--above { top: 195px; }
  .milestone-note--below { top: 482px; }
  .page-number {
    position: absolute;
    left: 1090px;
    top: 624px;
    width: 50px;
    height: 50px;
    border-radius: 50%;
    background: var(--navy);
    font-family: "Arimo", Arial, sans-serif;
    font-size: 14px;
    line-height: 50px;
    text-align: center;
  }
</style>
</head>
<body>
<main class="slide">
  <div class="slide__photo" role="img" aria-label="Background photograph of two business colleagues looking at a tablet, darkened"></div>

  <h1 class="slide__title">Lorem Ipsum is simply dummy</h1>

  <svg class="timeline" width="1200" height="675" viewBox="0 0 1200 675" aria-hidden="true">
    <defs>
      <polygon id="hex" points="-56,0 -28,-49 28,-49 56,0 28,49 -28,49"/>
    </defs>
    <line x1="0" y1="372" x2="1200" y2="372" stroke="#fff" stroke-width="2.5"/>

    <g stroke="#fff" stroke-width="1.2">
      <line x1="429" y1="292" x2="429" y2="319"/>
      <line x1="769" y1="292" x2="769" y2="319"/>
      <line x1="260" y1="424" x2="260" y2="456"/>
      <line x1="600" y1="424" x2="600" y2="456"/>
      <line x1="940" y1="424" x2="940" y2="456"/>
    </g>

    <g fill="#fff">
      <polygon points="336,361 360,372 336,383"/>
      <polygon points="506,361 530,372 506,383"/>
      <polygon points="675,361 699,372 675,383"/>
      <polygon points="846,361 870,372 846,383"/>
    </g>

    <g class="milestones" font-family="Open Sans, Arial, sans-serif" font-weight="700" font-size="19" text-anchor="middle" fill="#fff">
      <g transform="translate(259 372)">
        <use href="#hex" fill="var(--navy)" stroke="#fff" stroke-width="8" stroke-linejoin="round"/>
        <text y="7">2010</text>
      </g>
      <g transform="translate(429 372)">
        <use href="#hex" fill="var(--navy)" stroke="#fff" stroke-width="8" stroke-linejoin="round"/>
        <text y="7">2012</text>
      </g>
      <g transform="translate(599 372)">
        <use href="#hex" fill="var(--navy)" stroke="#fff" stroke-width="8" stroke-linejoin="round"/>
        <text y="7">2014</text>
      </g>
      <g transform="translate(769 372)">
        <use href="#hex" fill="var(--navy)" stroke="#fff" stroke-width="8" stroke-linejoin="round"/>
        <text y="7">2016</text>
      </g>
      <g transform="translate(938 372)">
        <use href="#hex" fill="var(--navy)" stroke="#fff" stroke-width="8" stroke-linejoin="round"/>
        <text y="7">2017</text>
      </g>
    </g>
  </svg>

  <p class="milestone-note milestone-note--above" style="left:309px">Lorem Ipsum is simply dummy text of the printing and typesetting industry.</p>
  <p class="milestone-note milestone-note--above" style="left:649px">Lorem Ipsum is simply dummy text of the printing and typesetting industry.</p>
  <p class="milestone-note milestone-note--below" style="left:140px">Lorem Ipsum is simply dummy text of the printing and typesetting industry.</p>
  <p class="milestone-note milestone-note--below" style="left:480px">Lorem Ipsum is simply dummy text of the printing and typesetting industry.</p>
  <p class="milestone-note milestone-note--below" style="left:820px">Lorem Ipsum is simply dummy text of the printing and typesetting industry.</p>

  <div class="page-number">10</div>
</main>
</body>
</html>
```